New Business Cards for Tormin Group

We need a new Business Card to compliment our new logo. We are a vibrant design, manufacture and install business providing recreation areas, public parks and Municipal spaces. We want business cards that are classy, modern and clean.

We have recently changed our logo, and are celebrating our 40th anniversary. We want business cards with a new modern design to reflect our status.

Target Market(s)

Customers

Contact Information for Business Card

We need all the details of our 3 offices as per the business card attached. Please disregard the old logo on the business card, the other three files show our new logo.

Requirements
Must have
• All info as per attached business card but with new logo.
Nice to have

```html
<!DOCTYPE html>
<html lang="en">
<head>
<meta charset="utf-8">
<title>Tormin Group – Business Card</title>
<link rel="stylesheet" href="https://fonts.googleapis.com/css2?family=Barlow:wght@400;500;600;700&display=swap">
<style>
  :root {
    --page: #e9e6e2;
    --card: #ffffff;
    --red: #e8323a;
    --charcoal: #4a4a4d;
    --ink: #555558;
    --white: #ffffff;
  }
  * { margin: 0; padding: 0; box-sizing: border-box; }
  html, body {
    width: 1200px; height: 989px; overflow: hidden;
    background: var(--page);
    font-family: "Barlow", Arial, sans-serif;
  }
  .card {
    position: absolute; left: 80px; top: 195px;
    width: 1040px; height: 600px;
    background: var(--card);
    box-shadow: 6px 8px 18px rgba(0,0,0,0.25);
  }
  .brand {
    position: absolute; left: 54px; top: 118px;
    display: flex; align-items: center; gap: 16px;
  }
  .brand-dot { width: 30px; height: 30px; border-radius: 50%; background: var(--red); }
  .brand-name {
    font-size: 52px; font-weight: 700; color: var(--charcoal);
    letter-spacing: 0.5px; line-height: 1;
  }
  .person {
    position: absolute; right: 52px; top: 124px; text-align: right;
  }
  .person-name { font-size: 40px; font-weight: 600; color: var(--red); line-height: 1.1; letter-spacing: 0.5px; }
  .person-title { font-size: 25px; font-weight: 400; color: var(--ink); letter-spacing: 0.6px; margin-top: 2px; }
  .offices {
    position: absolute; left: 0; top: 327px; width: 100%; height: 218px;
    background: var(--red);
  }
  .office { position: absolute; top: 18px; color: var(--white); }
  .office-head { font-size: 25px; font-weight: 700; letter-spacing: 0.3px; margin-bottom: 12px; }
  .office-address { font-size: 24px; font-weight: 400; letter-spacing: 0.4px; margin-bottom: 10px; }
  .office-line { display: flex; align-items: center; gap: 14px; font-size: 24px; letter-spacing: 0.3px; line-height: 32px; }
  .office-line svg { width: 22px; height: 20px; flex: none; }
  .office--head { left: 48px; }
  .office--dubai { left: 378px; }
  .office--qatar { left: 710px; }
  .footer {
    position: absolute; left: 0; bottom: 0; width: 100%; height: 50px;
    background: var(--charcoal); color: var(--white);
    font-size: 23px; letter-spacing: 0.4px;
    display: flex; align-items: center; justify-content: center;
  }
</style>
</head>
<body>
<svg width="0" height="0" style="position:absolute">
  <defs>
    <symbol id="icon-phone" viewBox="0 0 24 24"><path fill="#fff" d="M6.6 2.5l3 3.6-1.9 2.2c1.2 2.6 3.4 4.8 6 6l2.2-1.9 3.6 3-1.6 3.3c-.4.7-1.2 1-2 .8C9.2 18 4.9 13.8 3.3 6.1c-.2-.8.1-1.6.8-2z"/></symbol>
    <symbol id="icon-fax" viewBox="0 0 24 24"><path fill="#fff" d="M7 2h10v7H7zM3 10h18v9H3zM6 20h12v2H6z"/><rect x="6" y="13" width="12" height="2" fill="#e8323a"/></symbol>
    <symbol id="icon-mail" viewBox="0 0 24 24"><path fill="#fff" d="M2 5h20v14H2z"/><path fill="none" stroke="#e8323a" stroke-width="1.6" d="M2.5 5.5L12 13l9.5-7.5M2.5 18.5l7-6.5M21.5 18.5l-7-6.5"/></symbol>
  </defs>
</svg>

<main class="card">
  <div class="brand">
    <span class="brand-dot"></span>
    <span class="brand-name">Tormin Group</span>
  </div>

  <div class="person">
    <p class="person-name">Rami Kassab</p>
    <p class="person-title">Managing Partner</p>
  </div>

  <section class="offices">
    <div class="office office--head">
      <p class="office-head">Head office</p>
      <p class="office-address">31482 Abu Dhabi, U.A.E</p>
      <p class="office-line"><svg><use href="#icon-phone"/></svg>+971 (0)2 5530218</p>
      <p class="office-line"><svg><use href="#icon-fax"/></svg>+971 (0)2 5530219</p>
      <p class="office-line"><svg><use href="#icon-mail"/></svg>sales@tormingroup.com</p>
    </div>
    <div class="office office--dubai">
      <p class="office-head">Dubai Office</p>
      <p class="office-address">408216 Dubai, U.A.E.</p>
      <p class="office-line"><svg><use href="#icon-phone"/></svg>+971 (0)4 3187402</p>
      <p class="office-line"><svg><use href="#icon-fax"/></svg>+971(0)4 3187455</p>
      <p class="office-line"><svg><use href="#icon-mail"/></svg>sales@tormingroup.com</p>
    </div>
    <div class="office office--qatar">
      <p class="office-head">Qatar Office</p>
      <p class="office-address">17390 Doha, Qatar</p>
      <p class="office-line"><svg><use href="#icon-phone"/></svg>+974 44731586</p>
      <p class="office-line"><svg><use href="#icon-fax"/></svg>+974 44731590</p>
      <p class="office-line"><svg><use href="#icon-mail"/></svg>sales@tormingroup.com</p>
    </div>
  </section>

  <footer class="footer">P. +971 (0)50 384 7720&nbsp; E.rami@tormingroup.com&nbsp; W. www.tormingroup.com</footer>
</main>
</body>
</html>
```